Timber Crest Construction Needs business card

Hey we are in need of business card designs. I have upload our logo as a guideline, but free feel to run with it or come up with something unique.
Pls have fun with it and be creative. the name says it all!
i will give some directions after i see a few entries..
Updates
Logo source file has been uploaded..
Hey because of the logo is so colourful already.
Can we have a few submissions with less colour.
Also we are looking for clever/hidden/descriptive business card.

```html
<!DOCTYPE html>
<html lang="en">
<head>
<meta charset="utf-8">
<title>Timber Crest Construction – Business Card</title>
<link rel="stylesheet" href="https://fonts.googleapis.com/css2?family=Questrial&family=Montserrat:wght@700&display=swap">
<style>
  :root {
    --backdrop: #1f7d05;
    --card-white: #ffffff;
    --card-black: #1a1a1a;
    --accent-red: #e21d24;
    --brand-grey: #7d7e82;
    --text-light: #f2f2f2;
  }
  * { margin: 0; padding: 0; box-sizing: border-box; }
  html, body { width: 1200px; height: 1200px; overflow: hidden; }
  body {
    background: var(--backdrop);
    position: relative;
    font-family: "Questrial", sans-serif;
  }
  .card {
    position: absolute;
    width: 800px;
    height: 445px;
    overflow: hidden;
    background: var(--card-white);
  }
  .card--front { left: 212px; top: 130px; }
  .card--back { left: 220px; top: 649px; }

  .brand {
    position: absolute;
    display: flex;
    align-items: center;
    gap: 16px;
    color: var(--brand-grey);
    font-family: "Questrial", sans-serif;
    font-size: 34px;
    line-height: 1.1;
    letter-spacing: 1px;
    white-space: nowrap;
    transform: translate(-50%, -50%);
    z-index: 1;
  }
  .brand__square {
    width: 34px; height: 34px;
    background: var(--brand-grey);
    flex: none;
  }
  .brand__name { display: block; }
  .card--front .brand { left: 400px; top: 262px; }
  .card--back .brand { left: 196px; top: 255px; font-size: 30px; gap: 14px; }
  .card--back .brand__square { width: 30px; height: 30px; }

  .card__shape { position: absolute; inset: 0; }

  .contact {
    position: absolute;
    left: 478px;
    top: 114px;
    color: var(--text-light);
    font-size: 14px;
    letter-spacing: 2.6px;
  }
  .contact__name {
    font-family: "Montserrat", sans-serif;
    font-weight: 700;
    font-size: 15px;
    letter-spacing: 3.4px;
    line-height: 18px;
  }
  .contact__role { line-height: 26px; }
  .contact__address { margin-top: 42px; line-height: 21px; }
  .contact__list { list-style: none; margin-top: 38px; }
  .contact__item {
    display: flex;
    align-items: center;
    height: 25px;
  }
  .contact__icon { width: 16px; height: 16px; margin-right: 20px; flex: none; }
</style>
</head>
<body>
  <section class="card card--front">
    <div class="brand"><span class="brand__square"></span><span class="brand__name">TIMBER CREST<br>CONSTRUCTION</span></div>
  </section>

  <section class="card card--back">
    <svg class="card__shape" width="800" height="445" viewBox="0 0 800 445">
      <rect width="800" height="445" fill="var(--card-black)"/>
      <path d="M0,0 L360,0 C448,110 452,300 362,445 L0,445 Z" fill="var(--accent-red)"/>
      <path d="M0,0 L320,0 C420,100 450,300 362,445 L0,445 Z" fill="var(--card-white)"/>
    </svg>

    <div class="brand"><span class="brand__square"></span><span class="brand__name">TIMBER CREST<br>CONSTRUCTION</span></div>

    <div class="contact">
      <p class="contact__name">MARTA QUINN</p>
      <p class="contact__role">DIRECTOR</p>
      <p class="contact__address">SHOP 3, 212-216 HARBOUR<br>ROAD KINGSFORD NORTH</p>
      <ul class="contact__list">
        <li class="contact__item">
          <svg class="contact__icon" viewBox="0 0 16 16" fill="none" stroke="var(--accent-red)" stroke-width="1.6">
            <path d="M2 6 Q8 1 14 6 L12 7.5 L10.5 5.5 Q8 4.8 5.5 5.5 L4 7.5 Z"/><rect x="4" y="9" width="8" height="5" rx="1"/>
          </svg>5180 2714</li>
        <li class="contact__item">
          <svg class="contact__icon" viewBox="0 0 16 16" fill="none" stroke="var(--accent-red)" stroke-width="1.6">
            <rect x="4" y="1.5" width="8" height="4"/><rect x="1.5" y="5.5" width="13" height="6" rx="1"/><rect x="4" y="9.5" width="8" height="5"/>
          </svg>5180 2759</li>
        <li class="contact__item">
          <svg class="contact__icon" viewBox="0 0 16 16" fill="none" stroke="var(--accent-red)" stroke-width="1.6">
            <rect x="1.5" y="3.5" width="13" height="9"/><path d="M1.5 3.5 L8 9 L14.5 3.5"/>
          </svg>marta@northgable.com</li>
        <li class="contact__item">
          <svg class="contact__icon" viewBox="0 0 16 16" fill="none" stroke="var(--accent-red)" stroke-width="1.5">
            <circle cx="8" cy="8" r="6.3"/><ellipse cx="8" cy="8" rx="2.8" ry="6.3"/><path d="M1.7 8 H14.3 M3 4.5 H13 M3 11.5 H13"/>
          </svg>www.northgable.com</li>
      </ul>
    </div>
  </section>
</body>
</html>
```